Membership Drive "CHRISTMAS SPECIAL"

Looking to run a "Christmas Special" on 6 month Memberships for December 2019 to boost membership number up. This is a great time to get people exercising and everyone loves a Christmas Sale. Special is designed to attract more people to join and enjoy the savings.
Artwork will be display via social media (FP and Pictora) as well as in store. Artwork must be eye catching and direct to the customer. Customer should feel a sense of relief with being able to exercise at a lower cost .

Heading: "Christmas Sale"
6 Months
$199.00 Save over 30%
Terms and conditions apply"
*Offer End 31st December

below are other promos we had designed on Sketch Harbor along with potential photos to be included into this promo

Target Market(s)

Males and Females aged between 16 - 45

Industry/Entity Type

Fitness

Colors

Designer to choose colors to be used in the design.

Requirements
Must have
• Must emphasize "Christmas Special" $199.00 Save over 30%
• Terms and conditions apply
• Offer Ends 31st of December
• "All of our contact details"
• Address: 14 Marlow Rd Fernhill 3187
• Ph: 9428 7160
• www.stridelane.com.au
• Design format must come in PDF for a AO poster and an Pictora format please
Nice to have
• Some Christmas feels to the artwork

```html
<!DOCTYPE html>
<html lang="en">
<head>
<meta charset="utf-8">
<title>Stride Lane – Super Christmas Special</title>
<link rel="stylesheet" href="https://fonts.googleapis.com/css2?family=Josefin+Sans:wght@300;600;700&family=Montserrat:wght@700;800;900&family=Yellowtail&display=swap">
<style>
  :root {
    --festive-red: #e2334a;
    --pine-dark: #2f9a6c;
    --pine-mid: #48b06f;
    --pine-light: #8fd15a;
    --ink: #0b0b0b;
    --paper: #ffffff;
  }
  * { margin: 0; padding: 0; box-sizing: border-box; }
  html, body { width: 849px; height: 1200px; overflow: hidden; background: var(--festive-red); }
  .poster {
    position: relative;
    width: 849px;
    height: 1200px;
    overflow: hidden;
    background: var(--festive-red);
    font-family: "Josefin Sans", sans-serif;
  }
  .garland { position: absolute; left: 0; width: 849px; }
  .garland--top { top: 0; height: 250px; }
  .garland--bottom { bottom: 0; height: 240px; }

  .centered { position: absolute; left: 0; width: 849px; text-align: center; }

  .intro {
    top: 254px;
    font-weight: 300;
    font-size: 31px;
    line-height: 42px;
    color: var(--ink);
    padding-left: 8px;
  }
  .script-super {
    top: 338px;
    font-family: "Yellowtail", cursive;
    font-size: 150px;
    line-height: 170px;
    color: var(--paper);
    padding-left: 4px;
  }
  .headline {
    top: 462px;
    font-family: "Montserrat", sans-serif;
    font-weight: 900;
    font-size: 104px;
    line-height: 110px;
    color: var(--ink);
    letter-spacing: -1px;
    padding-left: 4px;
  }
  .subhead {
    top: 563px;
    font-weight: 300;
    font-size: 88px;
    line-height: 90px;
    color: var(--paper);
    padding-right: 12px;
  }
  .discount-band { position: absolute; left: 175px; top: 675px; width: 475px; height: 87px; }
  .discount-text {
    top: 683px;
    font-family: "Montserrat", sans-serif;
    font-weight: 800;
    font-size: 76px;
    line-height: 76px;
    color: var(--ink);
    padding-left: 8px;
  }
  .offer-end {
    position: absolute;
    top: 770px;
    left: 447px;
    font-weight: 600;
    font-size: 12px;
    color: var(--ink);
  }
  .price {
    top: 815px;
    font-family: "Montserrat", sans-serif;
    font-weight: 800;
    font-size: 70px;
    line-height: 74px;
    color: var(--paper);
  }
  .saving {
    top: 890px;
    font-weight: 700;
    font-size: 36px;
    line-height: 36px;
    color: var(--paper);
  }
  .saving-note {
    top: 926px;
    font-weight: 700;
    font-size: 18px;
    line-height: 20px;
    color: var(--paper);
  }

  .contact { position: absolute; left: 17px; top: 1086px; color: var(--paper); }
  .brand-name {
    font-family: "Montserrat", sans-serif;
    font-weight: 900;
    font-size: 25px;
    line-height: 48px;
    color: var(--ink);
    letter-spacing: 0.5px;
  }
  .contact-line {
    font-weight: 600;
    font-size: 11.5px;
    line-height: 21px;
    font-variant: small-caps;
  }
  .contact-line--web { font-variant: normal; font-size: 10px; text-transform: uppercase; }
  .terms {
    position: absolute;
    right: 17px;
    top: 1181px;
    font-weight: 600;
    font-size: 11px;
    font-variant: small-caps;
    color: var(--paper);
  }
</style>
</head>
<body>
<main class="poster">
  <svg class="garland garland--top" viewBox="0 0 849 250" role="img" aria-label="Border of green pine branches hanging along the top edge">
    <defs>
      <linearGradient id="pine-top" x1="0" y1="0" x2="0" y2="1">
        <stop offset="0" stop-color="#2f9a6c"/>
        <stop offset="0.6" stop-color="#48b06f"/>
        <stop offset="1" stop-color="#8fd15a"/>
      </linearGradient>
    </defs>
    <path fill="url(#pine-top)" d="M0 0H849V190L820 205L790 180L755 215L720 185L690 225L650 190L615 220L580 180L545 215L505 185L470 230L430 190L395 210L360 175L320 215L285 185L245 230L205 190L170 215L130 180L95 225L60 190L25 220L0 200Z"/>
  </svg>

  <p class="centered intro">Start your new year resolution with<br>our Christmas off</p>
  <p class="centered script-super">Super</p>
  <h1 class="centered headline">CHRISTMAS</h1>
  <p class="centered subhead">SPECIAL</p>

  <svg class="discount-band" viewBox="0 0 475 87" aria-hidden="true">
    <polygon points="24,0 475,0 449,87 0,87" fill="#ffffff"/>
  </svg>
  <p class="centered discount-text">30%OFF*</p>
  <p class="offer-end">Offer Ends 31st of December</p>

  <p class="centered price">$199.00</p>
  <p class="centered saving">SAVE OVER 30%</p>
  <p class="centered saving-note">WITH 6 MONTHS SUBSCRIPTION</p>

  <svg class="garland garland--bottom" viewBox="0 0 849 240" role="img" aria-label="Border of green pine branches along the bottom edge">
    <defs>
      <linearGradient id="pine-bottom" x1="0" y1="0" x2="0" y2="1">
        <stop offset="0" stop-color="#8fd15a"/>
        <stop offset="0.4" stop-color="#48b06f"/>
        <stop offset="1" stop-color="#2f9a6c"/>
      </linearGradient>
    </defs>
    <path fill="url(#pine-bottom)" d="M0 20L35 50L70 15L110 55L150 25L190 60L230 30L270 70L310 35L350 65L395 30L435 60L475 25L515 55L560 20L600 50L640 15L680 45L720 10L760 40L800 5L830 30L849 15V240H0Z"/>
  </svg>

  <section class="contact">
    <p class="brand-name">STRIDE LANE</p>
    <p class="contact-line">Address: 14 Marlow Rd Fernhill 3187</p>
    <p class="contact-line">Ph: 9428 7160</p>
    <p class="contact-line contact-line--web">www.stridelane.com.au</p>
  </section>
  <p class="terms">*Terms and conditions apply</p>
</main>
</body>
</html>
```